Vantor Wear and Fuel is looking for a Clothing/Supplement Online Store Website!

Must be convenient, and user friendly, with vibrant colors that catch the eye!

Target Market(s)

Athletes, and Fashion Customers

Industry/Entity Type

Fitness

Coding

Coded - Design and coding required

Number of Pages Required

3 page

Font styles to use
Decorative

Colors

Designer to choose colors to be used in the design.

Requirements
Must have
• Somewhere to feature products, features to promote discounts and make announcements.
Nice to have
• My logos on each page

```html
<!DOCTYPE html>
<html lang="en">
<head>
<meta charset="utf-8">
<title>Vantor Wear and Fuel</title>
<link href="https://fonts.googleapis.com/css2?family=Montserrat:wght@400;500;600;700;800;900&family=Open+Sans:wght@400;600;700&display=swap" rel="stylesheet">
<style>
:root{
  --violet:#3a1fa8;
  --violet-deep:#2a13a0;
  --violet-light:#5535c4;
  --orange:#fb6a1c;
  --ink:#222;
  --text:#444;
  --lavender:#e1dcf8;
  --footer:#1c1c1e;
  --footer-text:#8a8a8f;
  --line:#bdbdbd;
}
*{margin:0;padding:0;box-sizing:border-box}
html,body{width:1200px;height:2938px;overflow:hidden}
body{position:relative;background:#fff;font-family:"Montserrat",sans-serif;color:var(--ink)}
.abs{position:absolute}

/* header */
.brand{left:144px;top:40px;font-size:40px;font-weight:600;color:#555;letter-spacing:1px;display:flex;align-items:center;gap:12px}
.brand-mark{width:34px;height:34px;border-radius:50%;background:var(--violet)}
.search{left:741px;top:16px;width:240px;height:40px;border:1px solid #cfcfcf;display:flex;align-items:center;padding:0 14px;font-size:13px;color:#888;font-family:"Open Sans",sans-serif;justify-content:space-between}
.cart{left:1016px;top:16px;width:40px;height:40px;border-radius:50%;background:var(--violet);display:flex;align-items:center;justify-content:center}
.cart-count{left:1004px;top:17px;width:20px;height:20px;border-radius:50%;background:#111;color:#fff;font-size:10px;display:flex;align-items:center;justify-content:center;font-family:"Open Sans",sans-serif}
.nav{top:91px;right:145px;display:flex;gap:34px;font-size:13px;font-weight:500;color:#222}
.nav .active{color:var(--orange)}

/* hero */
.hero{left:0;top:144px;width:1200px;height:600px;clip-path:polygon(0 0,100% 0,100% 472px,806px 600px,0 472px);
  background:linear-gradient(180deg,#d3d6e0 0%,#c2c7d2 45%,#8d98a6 70%,#6f7c8a 100%)}
.hero-figure{left:700px;top:150px;width:340px;height:594px;background:linear-gradient(180deg,#3b3c40,#232427);border-radius:150px 150px 0 0;clip-path:polygon(0 0,100% 0,100% 556px,106px 594px,0 560px)}
.hero-kicker{left:143px;top:243px;font-size:25px;font-weight:500;color:#222}
.hero-pct{left:140px;top:268px;font-size:94px;font-weight:900;color:var(--violet);letter-spacing:-2px;line-height:1}
.hero-off{left:345px;top:281px;font-size:28px;font-weight:700;color:#222}
.hero-title{left:142px;top:362px;font-size:48px;font-weight:900;color:#222;line-height:48px}
.btn{background:var(--orange);color:#fff;font-family:"Open Sans",sans-serif;font-weight:700;font-size:14px;display:flex;align-items:center;justify-content:center}
.hero-btn{left:144px;top:471px;width:99px;height:40px}
.arrow{width:26px;height:30px}

/* welcome */
.welcome-title{left:0;width:1200px;top:816px;text-align:center;font-size:33px;font-weight:700;color:var(--violet)}
.welcome-text{left:140px;width:920px;top:860px;text-align:center;font-size:16.5px;line-height:27px;color:var(--text)}
.cats{left:144px;top:978px;display:flex;gap:18px}
.cat{width:168px;height:167px;border:1px solid #bcbcbc;display:flex;flex-direction:column;align-items:center;padding-top:30px;font-size:13.5px;font-weight:500;color:#222}
.cat svg{width:62px;height:62px;margin-bottom:22px}

/* featured */
.featured{left:0;top:1226px;width:1200px;height:584px;background:linear-gradient(100deg,var(--violet-deep),var(--violet-light));clip-path:polygon(0 0,100% 0,100% 458px,391px 584px,0 458px)}
.featured-title{left:0;width:1200px;top:1298px;text-align:center;color:#fff;font-size:33px;font-weight:600}
.products{left:144px;top:1362px;display:flex;gap:16px}
.product{width:216px;height:256px;background:#fff;display:flex;flex-direction:column;align-items:center;padding-top:22px}
.product-img{width:90px;height:120px;border-radius:8px}
.product-rule{width:56px;height:2px;background:var(--violet);margin-top:36px}
.product-name{font-size:13.5px;margin-top:13px;color:#222}
.product-price{font-size:13.5px;font-weight:700;color:var(--violet);margin-top:6px}

/* promos */
.promo{top:1891px;width:440px;height:280px}
.promo-a{left:144px;background:radial-gradient(circle at 45% 55%,#5a5048,#1f1f21 70%)}
.promo-b{left:615px;background:linear-gradient(90deg,#8a7f74,#b9aea2 55%,#6a6460)}
.promo-a-text{left:300px;width:267px;top:1906px;text-align:right;color:#fff;font-weight:600;font-size:16px;line-height:20px}
.promo-a-btn{left:467px;top:1952px;width:99px;height:40px}
.promo-b-title{left:631px;top:2065px;color:#fff;font-weight:800;font-size:20px;font-family:"Open Sans",sans-serif}
.promo-b-sub{left:631px;top:2088px;color:#fff;font-weight:600;font-size:16px;font-family:"Open Sans",sans-serif}
.promo-b-btn{left:631px;top:2116px;width:99px;height:40px}

/* newsletter */
.newsletter{left:0;top:2244px;width:1200px;height:343px;background:var(--lavender)}
.newsletter-title{left:0;width:1200px;top:2315px;text-align:center;font-size:33px;font-weight:600;color:var(--violet)}
.email{left:360px;top:2363px;width:380px;height:55px;background:var(--violet-deep);color:#fff;font-family:"Open Sans",sans-serif;font-size:14px;display:flex;align-items:center;padding-left:14px}
.subscribe{left:740px;top:2363px;width:100px;height:55px}

/* footer */
.footer{left:0;top:2458px;width:1200px;height:480px;background:var(--footer);clip-path:polygon(0 0,806px 129px,100% 0,100% 100%,0 100%)}
.foot-head{top:2638px;font-size:25px;color:var(--orange);font-weight:500}
.news{left:144px;width:300px;font-family:"Open Sans",sans-serif;font-size:11.5px;line-height:17px;color:var(--footer-text)}
.news b{display:block;color:#fff;font-weight:400;margin-bottom:3px}
.links{top:2684px;font-family:"Open Sans",sans-serif;font-size:11.5px;line-height:24px;color:var(--footer-text)}
.social{top:2687px;width:40px;height:40px;border-radius:50%;border:1px solid #8a8a8f}
.divider{left:144px;top:2868px;width:911px;height:1px;background:#3a3a3d}
.copyright{left:0;width:1200px;top:2896px;text-align:center;font-family:"Open Sans",sans-serif;font-size:11.5px;color:var(--footer-text)}
</style>
</head>
<body>

<header>
  <div class="abs brand"><span class="brand-mark"></span>VANTOR</div>
  <div class="abs search">Search
    <svg width="18" height="18" viewBox="0 0 18 18"><circle cx="7.5" cy="7.5" r="5.5" fill="none" stroke="#111" stroke-width="2.2"/><line x1="11.5" y1="11.5" x2="16" y2="16" stroke="#111" stroke-width="2.4"/></svg>
  </div>
  <div class="abs cart">
    <svg width="16" height="14" viewBox="0 0 16 14"><path d="M1 1h3l2 8h8l1-6H5" fill="none" stroke="#fff" stroke-width="2"/><circle cx="7" cy="12" r="1.4" fill="#fff"/><circle cx="13" cy="12" r="1.4" fill="#fff"/></svg>
  </div>
  <div class="abs cart-count">0</div>
  <nav class="abs nav">
    <span class="active">HOME</span><span>PRODUCTS</span><span>OFFERS</span><span>ABOUT US</span><span>NEWS</span><span>CONTACT US</span>
  </nav>
</header>

<section>
  <div class="abs hero" role="img" aria-label="Hero photo: a man in a dark hooded sweatshirt on a misty beach"></div>
  <div class="abs hero-figure" role="img" aria-label="Man in dark hoodie"></div>
  <div class="abs hero-kicker">FUSCE SOLLICITUDIN</div>
  <div class="abs hero-pct">15%</div>
  <div class="abs hero-off">Off</div>
  <div class="abs hero-title">Nulla<br>Facilisi</div>
  <div class="abs btn hero-btn">Shop Now</div>
  <svg class="abs arrow" style="left:51px;top:364px" viewBox="0 0 26 30"><path d="M17 4 7 15l10 11" fill="none" stroke="#fff" stroke-width="4"/></svg>
  <svg class="abs arrow" style="left:1121px;top:364px" viewBox="0 0 26 30"><path d="M9 4l10 11L9 26" fill="none" stroke="#fff" stroke-width="4"/></svg>
</section>

<section>
  <h1 class="abs welcome-title">WELCOME TO VANTOR WEAR AND FUEL</h1>
  <p class="abs welcome-text">Aliquam erat volutpat. Pellentesque blandit lacus eget nunc faucibus, et tincidunt eros viverra. Phasellus consequat sagittis nisi suscipit feugiat. Cras eget leo sed nunc hendrerit ultricies eu at nisl. Praesent iaculis faucibus urna sit amet lacinia. Maecenas consequat justo enim, ac mattis massa imperdiet quis.</p>
  <div class="abs cats">
    <div class="cat"><svg viewBox="0 0 62 62"><circle cx="26" cy="36" r="18" fill="none" stroke="#333" stroke-width="3.5"/><path d="M39 23 56 6M42 6h14v14" fill="none" stroke="#333" stroke-width="3.5"/></svg>Apparel for Men</div>
    <div class="cat"><svg viewBox="0 0 62 62"><circle cx="31" cy="22" r="16" fill="none" stroke="#333" stroke-width="3.5"/><path d="M31 38v22M22 50h18" fill="none" stroke="#333" stroke-width="3.5"/></svg>Apparel for Women</div>
    <div class="cat"><svg viewBox="0 0 62 62"><rect x="7" y="6" width="48" height="52" rx="10" fill="none" stroke="#333" stroke-width="3"/><path d="M15 24a16 12 0 0 1 32 0z" fill="none" stroke="#333" stroke-width="2.5"/><line x1="31" y1="24" x2="34" y2="14" stroke="#333" stroke-width="2.5"/><rect x="13" y="32" width="36" height="20" rx="3" fill="none" stroke="#333" stroke-width="2.5"/></svg>Weight Loss</div>
    <div class="cat"><svg viewBox="0 0 62 62"><path d="M16 58V40c0-8 6-14 14-14 2-6-2-10-4-14 4-6 12-6 14 0l-4 10c8 2 14 10 12 20-2 10-12 16-32 16z" fill="none" stroke="#333" stroke-width="3" stroke-linejoin="round"/></svg>Weight Gain</div>
    <div class="cat"><svg viewBox="0 0 62 62"><path d="M4 14h54M10 6v16M16 8v12M52 6v16M46 8v12" stroke="#333" stroke-width="3" fill="none"/><circle cx="31" cy="22" r="5" fill="none" stroke="#333" stroke-width="2.5"/><path d="M18 14l8 14h10l8-14M26 28l-2 14-8 16M36 28l2 14 8 16" fill="none" stroke="#333" stroke-width="2.5"/></svg>Strength</div>
  </div>
</section>

<section>
  <div class="abs featured"></div>
  <h2 class="abs featured-title">FEATURED PRODUCTS</h2>
  <div class="abs products">
    <div class="product"><div class="product-img" role="img" aria-label="Black athletic leggings" style="background:#2a2a2c;width:48px"></div><div class="product-rule"></div><div class="product-name">Cras sollicitudin</div><div class="product-price">$30.00</div></div>
    <div class="product"><div class="product-img" role="img" aria-label="Pouch of creatine powder" style="background:linear-gradient(180deg,#1e1e1e,#3a2a1c);width:70px;height:96px;margin-top:12px"></div><div class="product-rule" style="margin-top:48px"></div><div class="product-name">Etiam vel massa</div><div class="product-price">$20.00</div></div>
    <div class="product"><div class="product-img" role="img" aria-label="Black graphic t-shirt" style="background:#1c1c1c;width:118px;height:120px;border-radius:20px 20px 6px 6px"></div><div class="product-rule"></div><div class="product-name">Etiam mattis</div><div class="product-price">$22.00</div></div>
    <div class="product"><div class="product-img" role="img" aria-label="Tub of whey protein" style="background:linear-gradient(90deg,#111,#3a3a3a,#111);width:58px;height:88px;margin-top:16px"></div><div class="product-rule" style="margin-top:52px"></div><div class="product-name">Aliquam erat</div><div class="product-price">$26.00</div></div>
  </div>
  <svg class="abs arrow" style="left:51px;top:1475px" viewBox="0 0 26 30"><path d="M17 4 7 15l10 11" fill="none" stroke="#fff" stroke-width="4"/></svg>
  <svg class="abs arrow" style="left:1121px;top:1475px" viewBox="0 0 26 30"><path d="M9 4l10 11L9 26" fill="none" stroke="#fff" stroke-width="4"/></svg>
</section>

<section>
  <div class="abs promo promo-a" role="img" aria-label="Scoop of protein powder over a shaker with capsules on a dark table"></div>
  <div class="abs promo-a-text">MAECENAS VEL<br>TORTOR ACCUMSAN</div>
  <div class="abs btn promo-a-btn">Shop Now</div>
  <div class="abs promo promo-b" role="img" aria-label="Woman in a dark hoodie with earphones outdoors"></div>
  <div class="abs promo-b-title">PELLENTESQUE</div>
  <div class="abs promo-b-sub">blandit lacus eget</div>
  <div class="abs btn promo-b-btn">Shop Now</div>
</section>

<section>
  <div class="abs newsletter"></div>
  <h2 class="abs newsletter-title">NEWSLETTER SIGN UP</h2>
  <div class="abs email">Email Address</div>
  <div class="abs btn subscribe">Subscribe</div>
</section>

<footer>
  <div class="abs footer"></div>
  <h3 class="abs foot-head" style="left:144px">Latest News</h3>
  <div class="abs news" style="top:2684px"><b>22 October, 2019</b>Etiam massa elementum, bibendum tellus venenatis, feugiat massa. Curabitur venenatis lacinia ornare.</div>
  <div class="abs news" style="top:2764px"><b>22 October, 2019</b>Maecenas vel tortor accumsan quam varius imperdiet vel eget elit. Aenean facilisis tincidunt lectus.</div>
  <h3 class="abs foot-head" style="left:517px">Links</h3>
  <div class="abs links" style="left:519px">Home<br>Products<br>Offers<br>About Us<br>News<br>Contact Us</div>
  <div class="abs links" style="left:607px">My Account<br>Wishlist<br>My Cart<br>Checkout<br>Shipping<br>Returns</div>
  <div class="abs links" style="left:703px">Help<br>Privacy Policy<br>Terms and Conditions</div>
  <h3 class="abs foot-head" style="right:145px">Follow us on</h3>
  <div class="abs social" style="left:911px" aria-label="Social link"></div>
  <div class="abs social" style="left:963px" aria-label="Social link"></div>
  <div class="abs social" style="left:1015px" aria-label="Social link"></div>
  <div class="abs divider"></div>
  <div class="abs copyright">Copyright © 2019 &nbsp;Vantor Wear and Fuel. &nbsp;All rights reserved.</div>
</footer>

</body>
</html>
```